Residential Remodeling Contractor needs updated business card

I need a new design for my business card.
Name of the company is Ridgefell Construction. I need a card that commands presence, strength, integrity. I have been in business for 28 years. I am a Residential Remodeling Contractor that covers all aspects of a residential remodel and build.

```html
<!DOCTYPE html>
<html lang="en">
<head>
<meta charset="utf-8">
<title>Ridgefell Construction – Business Card</title>
<link rel="stylesheet" href="https://fonts.googleapis.com/css2?family=Noto+Serif:wght@400;600&display=swap">
<style>
  :root {
    --page-bg: #d4d5d7;
    --navy-deep: #1e3570;
    --navy-bright: #26478f;
    --ink-light: #ffffff;
    --ink-soft: #e6e9f2;
    --card-shadow: rgba(40, 44, 60, 0.35);
  }
  * { margin: 0; padding: 0; box-sizing: border-box; }
  html, body {
    width: 900px; height: 1200px; overflow: hidden;
    background: var(--page-bg);
    font-family: "Noto Serif", Georgia, serif;
  }
  .canvas { position: relative; width: 900px; height: 1200px; }
  .card {
    position: absolute; left: 133px; width: 633px; height: 364px;
    background: linear-gradient(120deg, var(--navy-deep) 0%, var(--navy-bright) 100%);
    color: var(--ink-light);
    overflow: hidden;
    box-shadow: 6px 8px 12px var(--card-shadow);
  }
  .card--front { top: 210px; }
  .card--back { top: 624px; background: linear-gradient(200deg, var(--navy-bright) 0%, var(--navy-deep) 60%); }

  .brand { position: absolute; left: 154px; top: 152px; display: flex; align-items: center; gap: 22px; }
  .brand__mark { width: 34px; height: 34px; background: var(--ink-light); flex: none; }
  .wordmark {
    font-weight: 600; font-variant: small-caps;
    font-size: 45px; line-height: 1.0; letter-spacing: 0.3px;
    color: var(--ink-light);
  }

  .symbol-area {
    position: absolute; left: 33px; top: 17px; width: 104px; height: 347px;
    background: linear-gradient(180deg, rgba(255,255,255,0.10) 0%, rgba(255,255,255,0.18) 100%);
  }

  .holder { position: absolute; left: 322px; top: 178px; }
  .holder__name {
    font-size: 27px; font-weight: 600; letter-spacing: 1px;
    text-transform: uppercase; line-height: 1.1;
  }
  .holder__role {
    font-size: 15px; letter-spacing: 0.6px; color: var(--ink-soft);
    margin-top: 4px;
  }
  .contacts { list-style: none; margin-top: 28px; }
  .contacts__item {
    display: flex; align-items: center; gap: 8px;
    font-size: 14.5px; letter-spacing: 0.9px; line-height: 23px;
    color: var(--ink-soft);
  }
  .contacts__icon { width: 15px; height: 15px; fill: var(--ink-light); flex: none; }
</style>
</head>
<body>
<main class="canvas">
  <section class="card card--front" aria-label="Card front">
    <div class="brand">
      <span class="brand__mark" aria-hidden="true"></span>
      <h1 class="wordmark">Ridgefell<br>Construction</h1>
    </div>
  </section>

  <section class="card card--back" aria-label="Card back">
    <div class="symbol-area" role="img" aria-label="Large brand symbol decoration"></div>
    <div class="holder">
      <p class="holder__name">Marco Delvane</p>
      <p class="holder__role">Residential Remodeling Contractor</p>
      <ul class="contacts">
        <li class="contacts__item">
          <svg class="contacts__icon" viewBox="0 0 24 24" aria-hidden="true"><path d="M6.6 10.8a15.1 15.1 0 0 0 6.6 6.6l2.2-2.2c.3-.3.7-.4 1-.2 1.1.4 2.3.6 3.6.6.6 0 1 .4 1 1V20c0 .6-.4 1-1 1A17 17 0 0 1 3 4c0-.6.4-1 1-1h3.5c.6 0 1 .4 1 1 0 1.3.2 2.5.6 3.6.1.3 0 .7-.2 1z"/></svg>
          <span>15550142287</span>
        </li>
        <li class="contacts__item">
          <svg class="contacts__icon" viewBox="0 0 24 24" aria-hidden="true"><path d="M2 5h20v14H2V5zm2 2v.3l8 6 8-6V7H4zm0 2.8V17h16V9.8l-8 6-8-6z"/></svg>
          <span>info@ridgefellconstruction.com</span>
        </li>
        <li class="contacts__item">
          <svg class="contacts__icon" viewBox="0 0 24 24" aria-hidden="true"><circle cx="12" cy="12" r="9.5" fill="none" stroke="#fff" stroke-width="2"/><ellipse cx="12" cy="12" rx="4" ry="9.5" fill="none" stroke="#fff" stroke-width="1.6"/><path d="M3 9h18v1.6H3zM3 13.4h18V15H3z"/></svg>
          <span>ridgefellconstruction.com</span>
        </li>
      </ul>
    </div>
  </section>
</main>
</body>
</html>
```